Simple and clean

We need a business card design for a new company called Dwelling Hawk. It is a search engine to find current properties for sale or rent in New Zealand market.
We have already a colour scheme that we would like people to use.
Light brown: #D4CCB0
Light green: #D6E4D4
Green: #669966
Black/White
It is OK to divert from this colour scheme slightly as long as there is a green component to the business card.
Final design should be clean, simple and should communicate the nature of the business.
Target Market(s)
- First home buyers
- Real estate agents
- People seeking rentals
Industry/Entity Type
Business
Requirements
Must have
- Use those or similar colours.
Light brown: #D4CCB0
Light green: #D6E4D4
Green: #669966
Black/White

```html
<!DOCTYPE html>
<html lang="en">
<head>
<meta charset="utf-8">
<title>Dwelling Hawk – Business Card</title>
<link rel="stylesheet" href="https://fonts.googleapis.com/css2?family=Source+Sans+3:ital,wght@0,400;0,700;1,400&display=swap">
<style>
  :root {
    --card-black: #000000;
    --card-sand: #d3d8ae;
    --brand-green: #5bbe45;
    --ink-dark: #111111;
    --url-grey: #a9a9a9;
    --edge-grey: #9a9a9a;
    --badge-fill: #e6e6e6;
    --badge-ring: #ffffff;
  }
  * { margin: 0; padding: 0; box-sizing: border-box; }
  html, body {
    width: 1200px;
    height: 702px;
    overflow: hidden;
    background: #ffffff;
  }
  .card {
    position: relative;
    width: 1200px;
    height: 702px;
    background: var(--card-black);
    border: 2px solid var(--edge-grey);
    overflow: hidden;
    font-family: "Source Sans 3", "Myriad Pro", Arial, sans-serif;
  }
  .card__sweep {
    position: absolute;
    inset: 0;
    width: 100%;
    height: 100%;
  }
  .brand {
    position: absolute;
    left: 50px;
    top: 48px;
    display: flex;
    align-items: center;
    gap: 12px;
  }
  .brand__badge {
    width: 166px;
    height: 166px;
    border-radius: 50%;
    background: var(--badge-fill);
    border: 6px solid var(--badge-ring);
    box-shadow: inset 0 0 0 3px #777;
    flex: none;
  }
  .brand__name {
    color: var(--brand-green);
    font-size: 76px;
    font-weight: 400;
    line-height: 1;
    letter-spacing: -0.5px;
    margin-top: -8px;
    white-space: nowrap;
  }
  .contact {
    position: absolute;
    right: 70px;
    top: 212px;
    text-align: right;
    color: var(--ink-dark);
  }
  .contact__name {
    font-size: 34px;
    font-weight: 700;
    line-height: 1.2;
  }
  .contact__role {
    font-size: 29px;
    font-style: italic;
    line-height: 1.2;
  }
  .contact__lines {
    margin-top: 42px;
    font-size: 28px;
    line-height: 1.55;
  }
  .web {
    position: absolute;
    left: 68px;
    top: 586px;
    color: var(--url-grey);
    font-size: 52px;
    line-height: 1;
    letter-spacing: 0.3px;
  }
</style>
</head>
<body>
  <div class="card">
    <svg class="card__sweep" viewBox="0 0 1084 634" preserveAspectRatio="none" aria-hidden="true">
      <path d="M1040,0 C720,40 540,190 540,312 C540,470 760,600 1064,634 L1084,634 L1084,0 Z" fill="var(--card-sand)"/>
    </svg>

    <div class="brand">
      <div class="brand__badge"></div>
      <div class="brand__name">Dwelling Hawk</div>
    </div>

    <div class="contact">
      <div class="contact__name">Sam Carter</div>
      <div class="contact__role">Director</div>
      <div class="contact__lines">
        <div class="contact__phone">Mobile: 04x-xxx-xxxx</div>
        <div class="contact__email">Email: s.carter@dwellinghawk.co.nz</div>
      </div>
    </div>

    <div class="web">www.dwellinghawk.co.nz</div>
  </div>
</body>
</html>
```